Wix Design for a Clothing Design Web Marketing Site

We need a Wix design and content (including any images and copy) for a clothing design web storefront, Sew To Suit (or sewtosuit). Rough ideas and content can be found at http://marenvoltis.wix.com/sewtosuit.

Sew To Suit is an innovative business concept that combines fashion and entertainment. The business model allows customers to actively participate in the creation of fashion designs/concepts , visualize the garment in the customer’s body in 3D, and buy the physical garment made specially to fit the customer.
The fashion consultant will be able to create the design based on client's desires and test various possibilities (size, fabric, cut, etc..) in front of the customer, using software Drapova (the software is a key component of this business model)
(when developing the website use images from Drapova)
After the design is created, the customer can choose to order the actual piece. The garment will be made according to the created design, the customer measurements.

Target Market(s)

Primarily women from 25 to 45, who are fashion enthusiasts and appreciate fit and exclusivity. They are hedonistic shoppers, who shop for entertainment.
Men (metrosexuals) who are fashion enthusiasts, also hedonistic shoppers.

Industry/Entity Type

Clothing

Font styles to use
Serif
Sans Serif

Requirements
Must have
• Must have a landing page (home) or section, that gives the consumer an idea of what Sew To Suit will do for them, an about page or section that tells about the company and product, a how it works page or section that describes how it works (http://marenvoltis.wix.com/sewtosuit#!services3/c192y), and page or section about pricing, and a page or section on how to contact us.
Nice to have
• Very modern and clean. The website must be based on the main picture of the studio in the example. If that studio is the store, what will the website look like?
• Colors yellow, grey and white. Use the zig zag in yellow and white. You can change the size of the lines. The zig zagi gives the modern and bold accent. Outfits in pictures must show nicely tailored garments.

```html
<!DOCTYPE html>
<html lang="en">
<head>
<meta charset="utf-8">
<title>Sew To Suit — Home</title>
<link rel="stylesheet" href="https://fonts.googleapis.com/css2?family=Lobster&family=Roboto:wght@400;500&display=swap">
<style>
  :root {
    --white: #ffffff;
    --ink: #2b2b2b;
    --text: #444444;
    --muted: #555555;
    --accent: #e8771f;
    --rule: #cfcfcf;
    --search-bg: #e6e6e6;
    --search-icon: #9a9a9a;
    --brand-yellow: #f4ef3a;
    --hero-light: #f4f2fb;
    --hero-mid: #dcd9ee;
    --hero-deep: #bdb9d9;
    --model-blue: #3a4fc0;
    --model-navy: #23307e;
    --model-skin: #e8c0a8;
    --model-chair: #4a2a22;
  }
  * { box-sizing: border-box; margin: 0; padding: 0; }
  html, body { width: 1200px; height: 855px; overflow: hidden; background: var(--white); }
  body { font-family: "Roboto", Arial, sans-serif; color: var(--text); position: relative; }

  .site-header { position: absolute; left: 0; top: 0; width: 1200px; height: 186px; }
  .brand {
    position: absolute; left: 110px; top: 15px; width: 127px; height: 96px;
    display: flex; align-items: center; gap: 8px;
  }
  .brand-mark { width: 14px; height: 14px; background: var(--brand-yellow); flex: none; }
  .brand-name { font-size: 17px; font-weight: 500; color: var(--ink); white-space: nowrap; }

  .search-button {
    position: absolute; left: 1049px; top: 42px; width: 38px; height: 38px;
    border-radius: 50%; background: var(--search-bg);
    display: flex; align-items: center; justify-content: center;
  }
  .header-rule { position: absolute; left: 110px; top: 126px; width: 977px; height: 1px; background: var(--rule); }

  .main-nav { position: absolute; left: 0; top: 146px; width: 1200px; font-size: 12.5px; color: var(--ink); }
  .main-nav a { position: absolute; top: 0; color: inherit; text-decoration: none; white-space: nowrap; }
  .main-nav a.is-current { color: var(--accent); }
  .nav-home { left: 110px; }
  .nav-about { left: 190px; }
  .nav-how { left: 343px; }
  .nav-price { left: 461px; }
  .nav-contact { left: 536px; }
  .cart-link { position: absolute; right: 113px; top: 146px; font-size: 12.5px; color: var(--ink); display: flex; align-items: center; gap: 3px; }

  .hero { position: absolute; left: 0; top: 186px; width: 1200px; height: 589px; overflow: hidden; }
  .hero-backdrop {
    position: absolute; inset: 0;
    background: radial-gradient(ellipse 70% 80% at 40% 55%, var(--hero-light) 0%, var(--hero-mid) 65%, var(--hero-deep) 100%);
  }
  .hero-model {
    position: absolute; left: 594px; top: 14px; width: 480px; height: 575px;
    border-radius: 200px 200px 0 0;
    background:
      linear-gradient(180deg, rgba(232,192,168,0.9) 0%, rgba(232,192,168,0.9) 44%, transparent 52%),
      linear-gradient(180deg, transparent 52%, var(--model-blue) 60%, var(--model-navy) 90%, var(--model-chair) 100%);
  }
  .hero-arrow { position: absolute; top: 267px; width: 30px; height: 60px; }
  .hero-arrow.prev { left: 25px; }
  .hero-arrow.next { left: 1146px; }
  .hero-title {
    position: absolute; left: 120px; top: 237px;
    font-family: "Lobster", "Georgia", cursive; font-size: 51px; font-weight: 400;
    color: #1e1e1e; line-height: 1;
  }
  .hero-text {
    position: absolute; left: 123px; top: 293px; width: 440px;
    font-size: 15.5px; line-height: 26px; color: #333333;
  }

  .site-footer { position: absolute; left: 0; top: 775px; width: 1200px; height: 80px; font-size: 12.5px; color: var(--muted); }
  .footer-links { position: absolute; left: 111px; top: 32px; }
  .footer-links a { color: inherit; text-decoration: none; }
  .footer-links .sep { margin: 0 5px; }
  .social { position: absolute; left: 553px; top: 30px; width: 95px; height: 18px; }
  .social-link { position: absolute; top: 0; height: 17px; border-radius: 3px; background: var(--accent); display: block; }
  .social-1 { left: 2px; width: 10px; }
  .social-2 { left: 26px; width: 10px; }
  .social-3 { left: 45px; width: 17px; }
  .social-4 { left: 77px; top: 3px; width: 14px; height: 14px; }
  .copyright { position: absolute; right: 111px; top: 32px; }
</style>
</head>
<body>
  <header class="site-header">
    <div class="brand"><span class="brand-mark"></span><span class="brand-name">Sew To Suit</span></div>
    <div class="search-button" aria-label="Search">
      <svg width="12" height="12" viewBox="0 0 12 12" fill="none" stroke="var(--search-icon)" stroke-width="1.6">
        <circle cx="5" cy="5" r="3.6"/><line x1="7.7" y1="7.7" x2="11" y2="11"/>
      </svg>
    </div>
    <div class="header-rule"></div>
    <nav class="main-nav">
      <a class="nav-home is-current" href="#">Home</a>
      <a class="nav-about" href="#">What is Sew To Suit?</a>
      <a class="nav-how" href="#">How it works</a>
      <a class="nav-price" href="#">Price</a>
      <a class="nav-contact" href="#">Contact Us</a>
    </nav>
    <div class="cart-link">My Cart (0 Items)
      <svg width="8" height="6" viewBox="0 0 8 6" fill="none" stroke="var(--ink)" stroke-width="1.2"><polyline points="1,1.5 4,4.5 7,1.5"/></svg>
    </div>
  </header>

  <section class="hero">
    <div class="hero-backdrop"></div>
    <div class="hero-model" role="img" aria-label="Studio photograph of a woman in a tailored blue plaid shirt with flowers in her hair, leaning on a wooden chair"></div>
    <svg class="hero-arrow prev" viewBox="0 0 30 60" fill="none" stroke="#3a3a3a" stroke-width="1.2"><polyline points="29,1 1,30 29,59"/></svg>
    <svg class="hero-arrow next" viewBox="0 0 30 60" fill="none" stroke="#3a3a3a" stroke-width="1.2"><polyline points="1,1 29,30 1,59"/></svg>
    <h1 class="hero-title">Be Inspired</h1>
    <p class="hero-text">Be inspired by the latest trends, iconic styles from all eras and the most prestigious fashion shows</p>
  </section>

  <footer class="site-footer">
    <div class="footer-links"><a href="#">Home</a><span class="sep">|</span><a href="#">What is Sew To Suit?</a><span class="sep">|</span><a href="#">More</a></div>
    <div class="social" aria-label="Social links">
      <a class="social-link social-1" href="#" aria-label="Social page"></a>
      <a class="social-link social-2" href="#" aria-label="Social page"></a>
      <a class="social-link social-3" href="#" aria-label="Video channel"></a>
      <a class="social-link social-4" href="#" aria-label="News feed"></a>
    </div>
    <div class="copyright">© 2015 by Sew To Suit. All Right Reserved.</div>
  </footer>
</body>
</html>
```